Business Cards for new orthopaedic surgery practice

My husband and I are starting our own orthopaedic surgery practice. We are looking for a business card that is uniform, but one will have my name/title and the other will have his. You can just create one design with my name on it for now. But when I choose your design as the winning design I will ask that you add another copy with his name/title.

We are looking for classy, simple, elite all in one. We like dark blues/a little gold/yellow. Something that goes with our logo. We want our logo incorporated. Here is all the info you need:
Business name: RV Bone & Vitality Center
Location: 38517 North Willowmere Ave
Maple Hollow, FL 33482
Phone: 954-218-4063
Fax: 954-582-7341
Email: info@myrvbonecare.example

Names: Lydia Vance, M.D.
Board Certified Hand and Upper Extremity Surgeon

Ebo Dansu, M.D.
Board Certified Hip & Knee Replacement/General Orthopaedic Surgeon

Can decide what you want to put on the back. Maybe a slogan:
Grounded in Care. Centered on You

I am just going to upload our logo. The only thing is if we select you as the winning design, the location, and phone numbers may change. We will need your help to update that once fully solidified.

Industry/Entity Type

Medical

Contact Information for Business Card

Colors
0054AA
0677BA
7BADD7
CADEEF
E8F1F8
0094D4
00A9DD
6FCCEA
C7EBF8
E9F6FB

Requirements
Must have
• class, appeal,
Should not have
• We want to air on the side of masculine if we are looking at masculine vs. feminine feel. But we still want it classy, sophisticated, and something we will love

```html
<!DOCTYPE html>
<html lang="en">
<head>
<meta charset="utf-8">
<title>RV Bone &amp; Vitality Center – Business Card</title>
<link rel="stylesheet" href="https://fonts.googleapis.com/css2?family=Marcellus&family=Lustria&display=swap">
<style>
  :root {
    --stage: #1c1c1c;
    --card-dark: #2b2b2c;
    --ink-dark: #141414;
    --navy: #243a8c;
    --cyan: #19a9dc;
    --edge: #1fb4e4;
    --text: #2a2a2a;
    --white: #ffffff;
  }
  * { margin: 0; padding: 0; box-sizing: border-box; }
  html, body { width: 953px; height: 1200px; overflow: hidden; }
  body {
    background: var(--stage);
    font-family: "Marcellus", serif;
    position: relative;
  }
  .card {
    position: absolute;
    left: 96px;
    width: 760px;
    height: 434px;
    border-bottom: 6px solid var(--edge);
    border-left: 3px solid var(--edge);
    box-shadow: 0 24px 50px rgba(0,0,0,.6);
  }
  .card-back { top: 110px; background: var(--card-dark); }
  .card-front { top: 640px; background: var(--white); }

  /* back */
  .back-brand {
    position: absolute; inset: 0;
    display: flex; align-items: center; justify-content: center; gap: 18px;
  }
  .back-brand .mark {
    width: 34px; height: 34px; border-radius: 50%; background: var(--ink-dark);
  }
  .back-brand .name {
    font-size: 40px; color: var(--ink-dark); letter-spacing: 1px; text-transform: uppercase;
  }

  /* front */
  .front-brand {
    position: absolute; top: 40px; right: 40px;
    display: flex; align-items: center; gap: 10px;
  }
  .front-brand .mark { width: 16px; height: 16px; background: var(--navy); border-radius: 50%; }
  .front-brand .name { font-size: 20px; color: var(--navy); text-transform: uppercase; letter-spacing: .5px; }

  .tagline {
    position: absolute; top: 132px; right: 60px;
    font-size: 34px; color: var(--navy); white-space: nowrap;
  }
  .tagline .accent { color: var(--cyan); }

  .doctor {
    position: absolute; top: 215px; right: 400px; text-align: right; width: 340px;
  }
  .doctor .doctor-name { font-size: 38px; color: var(--cyan); line-height: 1; }
  .doctor .credential { font-size: 15px; color: var(--cyan); margin-top: 2px; }
  .doctor .title {
    font-family: "Lustria", serif; font-size: 14.5px; color: var(--text);
    line-height: 1.3; margin-top: 10px;
  }
  .divider {
    position: absolute; left: 378px; top: 200px; width: 3px; height: 150px; background: var(--navy);
  }
  .contacts {
    position: absolute; left: 405px; top: 212px; list-style: none;
    font-family: "Lustria", serif; font-size: 16px; color: var(--text);
  }
  .contacts li { display: flex; align-items: center; gap: 16px; height: 32px; white-space: nowrap; }
  .contacts svg { width: 16px; height: 16px; flex: none; }
  .address {
    position: absolute; bottom: 34px; left: 0; right: 0; text-align: center;
    font-family: "Lustria", serif; font-size: 18px; color: var(--text);
  }
</style>
</head>
<body>

<section class="card card-back" aria-label="Card back">
  <div class="back-brand">
    <span class="mark"></span>
    <span class="name">RV Bone &amp; Vitality Center</span>
  </div>
</section>

<section class="card card-front" aria-label="Card front">
  <div class="front-brand">
    <span class="mark"></span>
    <span class="name">RV Bone &amp; Vitality Center</span>
  </div>

  <p class="tagline">Grounded in Care. <span class="accent">Centered</span> on You</p>

  <div class="doctor">
    <p class="doctor-name">Ebo Dansu</p>
    <p class="credential">M.D.</p>
    <p class="title">Board Certified Hip &amp; Knee<br>Replacement/General Orthopaedic<br>Surgeon</p>
  </div>

  <div class="divider"></div>

  <ul class="contacts">
    <li>
      <svg viewBox="0 0 16 16"><path fill="#19a9dc" d="M3.5 1.5l2.5 2.5-1.5 2a8 8 0 0 0 5.5 5.5l2-1.5 2.5 2.5-2 2C7 15 1 9 1.5 3.5z"/></svg>
      954-218-4063
    </li>
    <li>
      <svg viewBox="0 0 16 16"><rect x="4" y="1" width="8" height="14" rx="1.5" fill="none" stroke="#19a9dc" stroke-width="1.5"/></svg>
      954-582-7341
    </li>
    <li>
      <svg viewBox="0 0 16 16"><rect x="1" y="3" width="14" height="10" fill="#19a9dc"/><path d="M1 3l7 6 7-6" fill="none" stroke="#fff" stroke-width="1.2"/></svg>
      info@myrvbonecare.example
    </li>
    <li>
      <svg viewBox="0 0 16 16" fill="none" stroke="#19a9dc" stroke-width="1.2"><circle cx="8" cy="8" r="6.5"/><ellipse cx="8" cy="8" rx="3" ry="6.5"/><path d="M1.5 8h13M2.5 5h11M2.5 11h11"/></svg>
      www.myrvbonecare.example
    </li>
  </ul>

  <p class="address">38517 North Willowmere Ave, Maple Hollow, FL 33482</p>
</section>

</body>
</html>
```